Business Card Design for Technology Company

New business card design needed for technology company director.
Ideally, the design will fit the style and nature of the industry. We are a supplier of quality products and services, and we hope the design will give customers and suppliers this impression.

Target Market(s)

3D Printing Industry

Industry/Entity Type

Technology Equipment

Contact Information for Business Card

Name: Marcus Lin
Title: Director
Company address: Factory K4, 7B Harlowe Road, Springvale Victoria Australia 3150
Telephone: +61-3-8555 6413
Email: marcus.lin@vortalmake.com.au
Website: www.vortalmake.com.au

Requirements
Must have
• All information in business card details
• Company logo
• '3D Printers and 3D Print Filaments' at proper place
Nice to have
• Style to fit the industry
• Colour to fit logo

```html
<!DOCTYPE html>
<html lang="en">
<head>
<meta charset="utf-8">
<title>Vortal Make – Business Card</title>
<link href="https://fonts.googleapis.com/css2?family=Work+Sans:wght@400;500&display=swap" rel="stylesheet">
<style>
  :root {
    --backdrop: #141414;
    --card: #1f1f1f;
    --card-edge: #262626;
    --ink: #f2f2f2;
    --blue: #1b93d8;
    --orange: #f28a1c;
    --muted: #bdbdbd;
  }
  * { margin: 0; padding: 0; box-sizing: border-box; }
  html, body {
    width: 1200px; height: 900px; overflow: hidden;
    background: var(--backdrop);
    font-family: "Work Sans", Arial, sans-serif;
    color: var(--ink);
  }
  .stage {
    width: 1200px; height: 900px;
    display: flex; flex-direction: column;
    align-items: center; justify-content: center; gap: 40px;
  }
  .card {
    position: relative;
    width: 684px; height: 380px;
    background: linear-gradient(160deg, var(--card-edge), var(--card));
    box-shadow: 0 10px 30px rgba(0,0,0,.6);
  }
  .brand {
    position: absolute; left: 0; right: 0;
    display: flex; align-items: center; justify-content: center; gap: 18px;
  }
  .brand-mark { background: var(--orange); }
  .brand-name {
    font-weight: 500; letter-spacing: .18em; text-transform: uppercase;
    color: var(--ink); white-space: nowrap;
  }
  .card-front .brand { top: 150px; }
  .card-front .brand-mark { width: 56px; height: 56px; }
  .card-front .brand-name { font-size: 40px; }

  .tagline {
    position: absolute; left: 0; right: 0; top: 232px;
    text-align: center; font-size: 14px; font-weight: 400;
    letter-spacing: .14em; text-transform: uppercase; color: var(--muted);
    white-space: nowrap;
  }

  .card-back .brand { top: 52px; }
  .card-back .brand-mark { width: 44px; height: 44px; }
  .card-back .brand-name { font-size: 30px; }

  .person {
    position: absolute; left: 40px; top: 176px; width: 262px;
    text-align: right; white-space: nowrap;
  }
  .person-name {
    font-size: 32px; font-weight: 500; color: var(--blue);
    letter-spacing: .04em; text-transform: uppercase; line-height: 1.1;
  }
  .person-title { font-size: 18px; margin-top: 6px; }

  .divider {
    position: absolute; left: 318px; top: 172px;
    width: 2px; height: 80px; background: var(--orange);
  }
  .contacts {
    position: absolute; left: 338px; top: 168px;
    list-style: none; font-size: 17px; line-height: 30px; white-space: nowrap;
  }
  .contacts li { display: flex; align-items: center; gap: 12px; }
  .contacts svg { width: 14px; height: 14px; flex: none; }
  .accent { color: var(--orange); }

  .address {
    position: absolute; left: 0; right: 0; top: 300px;
    text-align: center; font-size: 17px; letter-spacing: .02em; white-space: nowrap;
  }
</style>
</head>
<body>
<main class="stage">
  <section class="card card-front">
    <div class="brand">
      <span class="brand-mark"></span>
      <span class="brand-name">Vortal Make</span>
    </div>
    <p class="tagline">3D Printers and 3D Print Filaments</p>
  </section>

  <section class="card card-back">
    <div class="brand">
      <span class="brand-mark"></span>
      <span class="brand-name">Vortal Make</span>
    </div>

    <div class="person">
      <p class="person-name">Marcus Lin</p>
      <p class="person-title">Director</p>
    </div>

    <div class="divider"></div>

    <ul class="contacts">
      <li>
        <svg viewBox="0 0 14 14" aria-hidden="true"><path d="M3 1 L5.5 1 L6.5 4 L5 5.2 C5.8 7 7 8.2 8.8 9 L10 7.5 L13 8.5 L13 11 C13 12 12 13 11 13 C5.5 12.5 1.5 8.5 1 3 C1 2 2 1 3 1 Z" fill="var(--blue)"/></svg>
        <span>+61-3-8555 6413</span>
      </li>
      <li>
        <svg viewBox="0 0 14 14" aria-hidden="true"><rect x="1" y="3" width="12" height="8" fill="none" stroke="var(--blue)" stroke-width="1.4"/><path d="M1 3 L7 8 L13 3" fill="none" stroke="var(--blue)" stroke-width="1.4"/></svg>
        <span>marcus.lin@vortalmake.com.au</span>
      </li>
      <li>
        <svg viewBox="0 0 14 14" aria-hidden="true"><circle cx="7" cy="7" r="6" fill="none" stroke="var(--blue)" stroke-width="1.2"/><ellipse cx="7" cy="7" rx="2.6" ry="6" fill="none" stroke="var(--blue)" stroke-width="1.1"/><path d="M1 7 H13" stroke="var(--blue)" stroke-width="1.1"/></svg>
        <span>www.<span class="accent">vortalmake</span>.com.au</span>
      </li>
    </ul>

    <p class="address">Factory K4, 7B Harlowe Road, Springvale Victoria Australia 3150</p>
  </section>
</main>
</body>
</html>
```